Quillmarsh Property Solutions need a business card design

Hello guys. We would need a business card design asap please.
We are a start up property investment business based in London UK specialised in buying, selling, managing and letting properties and helping distressed property owners.
The name of our Business is Quillmarsh, the logo symbolises the four fundamental elements of the world (earth, air, fire and water) and so it stands for strength, stability, longevity.
We would like the business card to communicate professionalism and reliability. Many many thanks indeed for your work.

Details:

1.) Rosalind Updike
Property Investor
Mobile: +44(0)7700123456
Email: rosalind.quillmarsh@mailbox-example.com

2.) Dominic Updike
Property Investor
Mobile: +44(0)7700987654
Email: dominic.quillmarsh@mailbox-example.com

```html
<!DOCTYPE html>
<html lang="en">
<head>
<meta charset="utf-8">
<title>Quillmarsh Property Solutions – Business Card</title>
<link rel="stylesheet" href="https://fonts.googleapis.com/css2?family=Montserrat:wght@400;600;800&family=Open+Sans:wght@400;600&display=swap">
<style>
  :root {
    --stage-bg: #e9e7e3;
    --card-bg: #ffffff;
    --ink: #141414;
    --ink-soft: #4a4a4a;
    --brand-green: #12a84a;
    --brand-blue-deep: #1d4fc4;
    --brand-blue-light: #5f9bf0;
    --icon-blue: #2f6fd8;
    --card-shadow: rgba(0, 0, 0, 0.18);
  }

  * { box-sizing: border-box; margin: 0; padding: 0; }

  html, body {
    width: 1200px;
    height: 720px;
    overflow: hidden;
    background: var(--stage-bg);
  }

  .stage {
    width: 1200px;
    height: 720px;
    display: flex;
    align-items: center;
    justify-content: center;
    gap: 40px;
  }

  .card {
    position: relative;
    width: 540px;
    height: 309px;
    background: var(--card-bg);
    box-shadow: 0 6px 18px var(--card-shadow);
    overflow: hidden;
    font-family: "Open Sans", Arial, sans-serif;
    color: var(--ink);
  }

  /* Front */
  .card-front__bands {
    position: absolute;
    inset: 0;
    width: 540px;
    height: 309px;
  }

  .holder {
    position: absolute;
    top: 8px;
    right: 22px;
    text-align: right;
    color: #ffffff;
  }
  .holder__name {
    font-family: "Open Sans", Arial, sans-serif;
    font-weight: 600;
    font-size: 17px;
    line-height: 1.2;
  }
  .holder__role {
    font-size: 11px;
    line-height: 1.3;
  }

  .brand {
    font-family: "Montserrat", Arial, sans-serif;
    font-weight: 800;
    color: var(--ink);
    letter-spacing: 0.06em;
    text-transform: uppercase;
  }
  .brand__name { display: block; line-height: 1; }
  .brand__tagline { display: block; line-height: 1.2; letter-spacing: 0.04em; }

  .card-front .brand {
    position: absolute;
    left: 40px;
    top: 150px;
  }
  .card-front .brand__name { font-size: 30px; }
  .card-front .brand__tagline { font-size: 12px; margin-top: 6px; padding-left: 26px; }

  .contact {
    position: absolute;
    left: 40px;
    bottom: 26px;
    list-style: none;
    font-size: 13px;
    color: var(--ink-soft);
  }
  .contact__item {
    display: flex;
    align-items: center;
    gap: 8px;
    line-height: 1.7;
  }
  .contact__icon { width: 12px; height: 12px; flex: none; }

  /* Back */
  .card-back {
    display: flex;
    flex-direction: column;
    align-items: center;
    justify-content: center;
  }
  .card-back .brand { text-align: center; margin-top: -20px; }
  .card-back .brand__name { font-size: 36px; }
  .card-back .brand__tagline { font-size: 14px; margin-top: 8px; }

  .website {
    position: absolute;
    bottom: 40px;
    left: 0;
    right: 0;
    text-align: center;
    font-size: 17px;
    letter-spacing: 0.08em;
    color: var(--ink-soft);
  }
</style>
</head>
<body>
<main class="stage">

  <section class="card card-front" aria-label="Business card front">
    <svg class="card-front__bands" viewBox="0 0 540 309" aria-hidden="true">
      <defs>
        <linearGradient id="blue-wedge" x1="0" y1="0" x2="1" y2="0.3">
          <stop offset="0" stop-color="var(--brand-blue-deep)"/>
          <stop offset="1" stop-color="var(--brand-blue-light)"/>
        </linearGradient>
      </defs>
      <polygon class="band-green" points="205,0 540,0 540,56 228,50" fill="var(--brand-green)"/>
      <path class="band-blue" d="M228,50 L540,56 V64 C508,68 492,96 506,128 Z" fill="url(#blue-wedge)"/>
    </svg>

    <div class="holder">
      <p class="holder__name">Rosalind Updike</p>
      <p class="holder__role">Property Investor</p>
    </div>

    <p class="brand">
      <span class="brand__name">Quillmarsh</span>
      <span class="brand__tagline">Property Solutions</span>
    </p>

    <ul class="contact">
      <li class="contact__item">
        <svg class="contact__icon" viewBox="0 0 12 12" aria-hidden="true">
          <rect x="3" y="0.5" width="6" height="11" rx="1.2" fill="var(--icon-blue)"/>
          <rect x="4" y="2" width="4" height="6" fill="#ffffff"/>
          <circle cx="6" cy="9.8" r="0.7" fill="#ffffff"/>
        </svg>
        <span>+44(0)7700123456</span>
      </li>
      <li class="contact__item">
        <svg class="contact__icon" viewBox="0 0 12 12" aria-hidden="true">
          <circle cx="6" cy="6" r="6" fill="var(--icon-blue)"/>
          <rect x="2.8" y="3.8" width="6.4" height="4.4" fill="#ffffff"/>
          <polyline points="2.8,3.8 6,6.4 9.2,3.8" fill="none" stroke="var(--icon-blue)" stroke-width="0.8"/>
        </svg>
        <span>rosalind.quillmarsh@mailbox-example.com</span>
      </li>
    </ul>
  </section>

  <section class="card card-back" aria-label="Business card back">
    <p class="brand">
      <span class="brand__name">Quillmarsh</span>
      <span class="brand__tagline">Property Solutions</span>
    </p>
    <p class="website">www.quillmarsh-example.com</p>
  </section>

</main>
</body>
</html>
```